New Business Card Design Project

We would like a business card that represents the sale of boat, home, auto, and life insurance.

The logo can change colors to meet the look of the design if needed.

Industry/Entity Type

Business

```html
<!DOCTYPE html>
<html lang="en">
<head>
<meta charset="utf-8">
<title>Norvale Financial – Business Cards</title>
<link rel="stylesheet" href="https://fonts.googleapis.com/css2?family=Arimo:wght@400;700&family=Didact+Gothic&display=swap">
<style>
  :root {
    --backdrop: #2b2b2b;
    --card: #ffffff;
    --card-shade: #e9e9e9;
    --ink: #2a2a2a;
    --grey: #5c5c5c;
    --brand-blue: #3d6c82;
    --edge-grey: #6f6f6f;
  }
  * { margin: 0; padding: 0; box-sizing: border-box; }
  html, body { width: 1200px; height: 997px; overflow: hidden; }
  body { background: var(--backdrop); position: relative; }

  .card {
    position: absolute;
    width: 520px;
    height: 297px;
    background: linear-gradient(160deg, var(--card) 40%, var(--card-shade) 100%);
    box-shadow: 0 10px 30px rgba(0,0,0,.55);
    overflow: hidden;
  }
  .card--front { left: 90px; top: 110px; }
  .card--back  { left: 590px; top: 560px; }

  .card__band { position: absolute; left: 0; bottom: 0; width: 520px; height: 30px; }

  .brand { text-align: center; position: absolute; left: 0; right: 0; }
  .brand__name {
    font-family: "Didact Gothic", sans-serif;
    font-size: 34px;
    letter-spacing: 6px;
    color: var(--grey);
    display: inline-flex;
    align-items: center;
    gap: 12px;
  }
  .brand__dot { width: 14px; height: 14px; border-radius: 50%; background: var(--brand-blue); }
  .brand__tagline {
    font-family: "Didact Gothic", sans-serif;
    font-size: 17px;
    letter-spacing: 2.5px;
    color: var(--ink);
    margin-top: 4px;
  }
  .card--front .brand { top: 70px; }
  .card--back .brand { top: 40px; }

  .services {
    position: absolute;
    left: 0; right: 0; bottom: 54px;
    display: flex;
    justify-content: center;
    align-items: center;
    gap: 16px;
    font-family: "Didact Gothic", sans-serif;
    font-size: 13px;
    letter-spacing: 3px;
    color: var(--grey);
  }
  .services__rule { width: 2px; height: 20px; background: var(--brand-blue); }

  .person { position: absolute; left: 40px; bottom: 62px; font-family: "Arimo", sans-serif; font-weight: 700; }
  .person__name { font-size: 20px; color: var(--ink); }
  .person__role { font-size: 14px; color: var(--brand-blue); margin-top: 2px; }

  .divider {
    position: absolute; left: 270px; top: 150px; width: 2px; height: 96px;
    background: linear-gradient(to bottom, transparent, var(--grey), transparent);
  }

  .contacts { position: absolute; left: 290px; top: 150px; list-style: none; font-family: "Arimo", sans-serif; font-size: 12.5px; color: var(--ink); }
  .contacts__item { display: flex; align-items: center; gap: 12px; height: 22px; }
  .contacts__icon { width: 14px; height: 14px; flex: none; }
</style>
</head>
<body>

  <section class="card card--front">
    <div class="brand">
      <div class="brand__name"><span class="brand__dot"></span>NORVALE FINANCIAL</div>
      <div class="brand__tagline">investments &amp; insurance</div>
    </div>
    <div class="services">
      <span>BOAT</span><span class="services__rule"></span>
      <span>HOME</span><span class="services__rule"></span>
      <span>AUTO</span><span class="services__rule"></span>
      <span>LIFE INSURANCE</span>
    </div>
    <svg class="card__band" viewBox="0 0 520 30" aria-hidden="true">
      <path d="M0 30 L0 24 L330 24 Q340 8 362 6 L520 6 L520 30 Z" fill="var(--edge-grey)"/>
      <path d="M330 24 Q340 8 362 6 L520 6 L520 16 L372 16 Q352 17 344 24 Z" fill="var(--brand-blue)"/>
    </svg>
  </section>

  <section class="card card--back">
    <div class="brand">
      <div class="brand__name"><span class="brand__dot"></span>NORVALE FINANCIAL</div>
      <div class="brand__tagline">investments &amp; insurance</div>
    </div>

    <div class="person">
      <div class="person__name">DANIEL MARSH</div>
      <div class="person__role">MANAGING DIRECTOR</div>
    </div>

    <div class="divider"></div>

    <ul class="contacts">
      <li class="contacts__item">
        <svg class="contacts__icon" viewBox="0 0 14 14" aria-hidden="true"><path d="M1 5 Q7 0 13 5 L11 7 L9 5.5 L5 5.5 L3 7 Z M3 8 L11 8 L12 13 L2 13 Z" fill="var(--grey)"/></svg>
        +61 400 218 764
      </li>
      <li class="contacts__item">
        <svg class="contacts__icon" viewBox="0 0 14 14" aria-hidden="true"><rect x="1" y="3" width="12" height="9" fill="var(--grey)"/><path d="M1 3 L7 8 L13 3" stroke="#fff" stroke-width="1.2" fill="none"/></svg>
        daniel@harbourline.com.au
      </li>
      <li class="contacts__item">
        <svg class="contacts__icon" viewBox="0 0 14 14" aria-hidden="true"><rect x="1" y="5" width="7" height="4" rx="2" transform="rotate(-45 4.5 7)" stroke="var(--grey)" stroke-width="1.5" fill="none"/><rect x="6" y="5" width="7" height="4" rx="2" transform="rotate(-45 9.5 7)" stroke="var(--grey)" stroke-width="1.5" fill="none"/></svg>
        www.harbourline.com.au
      </li>
      <li class="contacts__item">
        <svg class="contacts__icon" viewBox="0 0 14 14" aria-hidden="true"><circle cx="7" cy="7" r="5" fill="var(--brand-blue)"/></svg>
        social.harbourline.com.au
      </li>
    </ul>

    <svg class="card__band" viewBox="0 0 520 30" aria-hidden="true">
      <path d="M0 30 L0 24 L330 24 Q340 8 362 6 L520 6 L520 30 Z" fill="var(--edge-grey)"/>
      <path d="M330 24 Q340 8 362 6 L520 6 L520 16 L372 16 Q352 17 344 24 Z" fill="var(--brand-blue)"/>
    </svg>
  </section>

</body>
</html>
```